Brightfield Homes needs a web design and brand identifier

Brightfield Homes is a pioneering approach by Northvale councils and four greenhouse alliances to support low income households to install solar systems with no upfront costs.

Brightfield Homes will commence in May 2017.

Brightfield Homes is looking for a designer to create a website banner incorporating a brand identifier for Brightfield Homes. The brand identifier will be used in Brightfield Homes promotional materials, such as flyers and mail outs.

The website banner and brand identifier should engender trust and confidence in the target group (retirees).

Reason: Hi, Thank you for your work so far. We've been given advice to get a separate logo designed (instead of trying to include this as part of the banner design). Sorry for not realising this until now - we're new to all this. So, I have a couple of preliminary logo designs that are being considered by our project control group. I will forward a copy of the logo once we have it. The project control group is looking for a web design that is unique to Brightfield Homes and a design that draws on the key elements of the program (i.e. it helps people save money and take control). The site should be friendly but not too informal as the target group is seniors. Here's a link to another community energy organisation: www.kindlewattnet.com.au/ Apologies again for the delays. Cheers, Doug

Target Market(s)

Home owning, low income, retirees

Industry/Entity Type

Non Profit

Number of Pages Required

1 page

Font styles to use
Sans Serif

Requirements
Must have
• Use of Brightfield Home name
• Must promote Brightfield Homes as safe, reliable and trustworthy
Nice to have
• Blue - to engender sense of safety and confidence (open to suggestions, though)
• Solar panels / the sun
Should not have
• Anything that is hard to read
• anything that promotes riskyness

```html
<!DOCTYPE html>
<html lang="en">
<head>
<meta charset="utf-8">
<title>Brightfield Homes</title>
<link rel="stylesheet" href="https://fonts.googleapis.com/css2?family=Montserrat:wght@400;600;700;800&family=Federo&family=Crimson+Text&family=Open+Sans:wght@400;600;700&display=swap">
<style>
:root{
  --blue:#0a5fd8;
  --blue-band:rgba(40,110,215,.88);
  --grey-bg:#f5f5f5;
  --footer-bg:#f2f2f2;
  --box-grey:#e6e6e6;
  --ink:#2b2b2b;
  --muted:#555;
  --soft:#666;
  --line:#e2e2e2;
  --white:#fff;
}
*{margin:0;padding:0;box-sizing:border-box}
html,body{width:1200px;height:2278px;overflow:hidden;background:var(--white)}
body{position:relative;font-family:"Open Sans",sans-serif;color:var(--ink)}
.abs{position:absolute}
.site-header{left:0;top:0;width:1200px;height:82px;background:var(--blue)}
.brand{left:99px;top:24px;font:800 27px "Montserrat",sans-serif;color:var(--white);letter-spacing:.3px;white-space:nowrap}
.nav{left:0;top:34px;width:1200px}
.nav a{position:absolute;font:700 12.5px "Montserrat",sans-serif;color:var(--white);text-decoration:none;white-space:nowrap}
.intro{left:0;top:82px;width:1200px;height:825px;background:var(--grey-bg)}
.hero-photo{left:99px;top:91px;width:1002px;height:498px;background:linear-gradient(135deg,#c9d6dd 0%,#e8e2cf 35%,#d9c060 60%,#b9cbd8 100%)}
.hero-band{left:99px;top:451px;width:1002px;height:138px;background:var(--blue-band)}
.hero-title{right:137px;top:465px;font:400 36px "Federo",sans-serif;color:var(--white);letter-spacing:1px}
.hero-text{right:137px;top:516px;width:740px;text-align:right;font:400 21px/27px "Crimson Text",serif;color:var(--white)}
.hero-btn{left:136px;top:522px;width:152px;height:44px;border:1px solid var(--white);color:var(--white);font:400 15px/42px "Federo",sans-serif;text-align:center;letter-spacing:.5px}
.dot{width:23px;height:23px;border-radius:50%;background:var(--white)}
.section-title{font:400 34px "Federo",sans-serif;color:var(--ink);letter-spacing:1px;white-space:nowrap}
.center{left:0;width:1200px;text-align:center}
.feature h3{position:absolute;font:400 21px "Federo",sans-serif;color:var(--ink);letter-spacing:.5px}
.feature p{position:absolute;width:225px;font:400 10.5px/17px "Open Sans",sans-serif;color:var(--muted)}
.feature .more{position:absolute;font:600 12.5px "Open Sans",sans-serif;color:var(--ink)}
.divider{width:1px;background:var(--line)}
.list li{position:absolute;list-style:none;font:400 13.5px/22px "Open Sans",sans-serif;color:var(--ink)}
.list svg{position:absolute;left:-28px;top:3px}
.media{background:linear-gradient(180deg,#3aa5ee 0%,#6fc2f5 55%,#8ac63e 80%,#e9c8b0 100%)}
.people-photo{background:linear-gradient(135deg,#cfd4d8 0%,#f1efec 45%,#9fa7ad 100%)}
.play{width:66px;height:66px;border-radius:50%;background:var(--white)}
.subhead{font:600 23px "Open Sans",sans-serif;color:var(--ink)}
.body-copy{font:400 17px/30px "Open Sans",sans-serif;color:var(--ink)}
.contact-box{left:229px;top:1890px;width:740px;height:55px;background:var(--box-grey)}
.contact-box span{position:absolute;top:13px;font:400 23px "Open Sans",sans-serif;color:var(--ink);white-space:nowrap}
.site-footer{left:0;top:1981px;width:1200px;height:255px;background:var(--footer-bg)}
.footer-title{font:600 23px "Open Sans",sans-serif;color:var(--ink)}
.footer-link{font:400 12px "Open Sans",sans-serif;color:var(--soft)}
.footer-text{font:400 11.5px/20px "Open Sans",sans-serif;color:var(--ink);white-space:nowrap}
.newsletter-input{left:343px;top:2066px;width:155px;height:33px;border:1px solid #ccc;background:var(--white);font:400 11.5px/31px "Open Sans",sans-serif;color:var(--soft);padding-left:10px}
.newsletter-btn{left:498px;top:2066px;width:71px;height:33px;background:#1f6fc7;color:var(--white);font:700 12px/33px "Open Sans",sans-serif;text-align:center}
.social-sq{width:27px;height:27px;border-radius:2px}
.copyright{left:0;top:2250px;width:1200px;text-align:center;font:400 10.5px "Open Sans",sans-serif;color:var(--ink)}
</style>
</head>
<body>

<header class="site-header abs">
  <div class="brand abs">BRIGHTFIELD HOMES</div>
  <nav class="nav abs">
    <a style="left:478px">HOME</a>
    <a style="left:540px">ABOUT US</a>
    <a style="left:628px">HOW IT WORKS</a>
    <a style="left:752px">WHO IS BRIGHTFIELD HOME?</a>
    <a style="left:988px">CONTACT US</a>
  </nav>
</header>

<section class="intro abs"></section>

<div class="hero-photo abs" role="img" aria-label="Senior woman relaxing on a yellow sofa using a tablet"></div>
<div class="dot abs" style="left:987px;top:405px"></div>
<div class="dot abs" style="left:1022px;top:405px"></div>
<svg class="abs" style="left:994px;top:411px" width="10" height="11"><path d="M6 2 L3 5.5 L6 9" stroke="#333" stroke-width="1.6" fill="none"/></svg>
<svg class="abs" style="left:1029px;top:411px" width="10" height="11"><path d="M4 2 L7 5.5 L4 9" stroke="#333" stroke-width="1.6" fill="none"/></svg>
<div class="hero-band abs"></div>
<div class="hero-title abs">WE NEED YOU</div>
<p class="hero-text abs">Help pensioner households to save money and take control of their energy bills by installing an affordable, quality solar system and be part of an Australian first.</p>
<div class="hero-btn abs">READ MORE</div>

<h2 class="section-title abs center" style="top:622px">BRIGHTFIELD HOMES</h2>

<div class="feature">
  <svg class="abs" style="left:97px;top:722px" width="72" height="70" viewBox="0 0 72 70">
    <path d="M30 4 L54 12 V34 C54 50 44 60 30 66 C16 60 6 50 6 34 V12 Z" fill="none" stroke="#1565d8" stroke-width="6"/>
    <circle cx="54" cy="53" r="15" fill="#1565d8"/>
    <path d="M46 53 L52 59 L62 47" stroke="#fff" stroke-width="4" fill="none"/>
  </svg>
  <h3 style="left:180px;top:726px">SAFE</h3>
  <p style="left:180px;top:769px">Lorem ipsum dolor sit amet, consectetur adipiscing elit, sed do eiusmod tempor incididunt ut labore et dolore magna aliqua...</p>
  <div class="more" style="left:180px;top:826px">Read more &nbsp;»</div>

  <div class="divider abs" style="left:424px;top:720px;height:165px"></div>

  <svg class="abs" style="left:441px;top:730px" width="88" height="56" viewBox="0 0 88 56">
    <path d="M4 14 L22 6 L44 14 L66 6 L84 14 L78 34 L58 50 L44 40 L30 50 L10 34 Z" fill="#8a8a8a"/>
  </svg>
  <h3 style="left:534px;top:726px">RELIABLE</h3>
  <p style="left:534px;top:769px">Lorem ipsum dolor sit amet, consectetur adipiscing elit, sed do eiusmod tempor incididunt ut labore et dolore magna aliqua...</p>
  <div class="more" style="left:534px;top:826px">Read more &nbsp;»</div>

  <div class="divider abs" style="left:776px;top:720px;height:165px"></div>

  <svg class="abs" style="left:796px;top:722px" width="56" height="76" viewBox="0 0 56 76">
    <path d="M16 44 L8 72 L18 66 L24 74 L28 50 Z M40 44 L48 72 L38 66 L32 74 L28 50 Z" fill="#8a8a8a"/>
    <circle cx="28" cy="26" r="24" fill="#8a8a8a"/>
    <circle cx="28" cy="26" r="16" fill="#fff"/>
    <circle cx="28" cy="26" r="9" fill="#8a8a8a"/>
  </svg>
  <h3 style="left:873px;top:726px">TRUSTWORTHY</h3>
  <p style="left:879px;top:769px">Lorem ipsum dolor sit amet, consectetur adipiscing elit, sed do eiusmod tempor incididunt ut labore et dolore magna aliqua...</p>
  <div class="more" style="left:879px;top:826px">Read more &nbsp;»</div>
</div>

<h2 class="section-title abs" style="left:137px;top:939px">HOW IT WORKS</h2>
<ul class="list">
  <li style="left:164px;top:1004px;width:420px"><svg width="16" height="14"><path d="M2 12 C2 6 6 5 11 5 V2 L15 6.5 L11 11 V8 C7 8 4 9 2 12Z" fill="#333"/></svg>Brightfield Homes checks that every person gets a solar system that pays for itself in energy savings from day one</li>
  <li style="left:164px;top:1068px;width:420px"><svg width="16" height="14"><path d="M2 12 C2 6 6 5 11 5 V2 L15 6.5 L11 11 V8 C7 8 4 9 2 12Z" fill="#333"/></svg>Brightfield Homes organises for the solar system to be installed</li>
  <li style="left:164px;top:1109px;width:420px"><svg width="16" height="14"><path d="M2 12 C2 6 6 5 11 5 V2 L15 6.5 L11 11 V8 C7 8 4 9 2 12Z" fill="#333"/></svg>Brightfield Homes supports pensioners to understand and get the most out of solar</li>
  <li style="left:164px;top:1177px;width:420px"><svg width="16" height="14"><path d="M2 12 C2 6 6 5 11 5 V2 L15 6.5 L11 11 V8 C7 8 4 9 2 12Z" fill="#333"/></svg>Pensioners gradually pay for cost through their usual rates payments at 0% interest</li>
</ul>

<div class="media abs" style="left:608px;top:927px;width:458px;height:316px" role="img" aria-label="Video still: hands holding a small green world with wind turbines, solar panels and city buildings"></div>
<div class="play abs" style="left:804px;top:1048px"></div>
<svg class="abs" style="left:828px;top:1065px" width="26" height="32"><path d="M2 2 L24 16 L2 30 Z" fill="#555"/></svg>

<div class="people-photo abs" style="left:126px;top:1281px;width:459px;height:317px" role="img" aria-label="Advisor talking with a senior couple at home"></div>

<h2 class="section-title abs" style="left:623px;top:1297px">IS MY CLIENT ELIGIBLE?</h2>
<div class="subhead abs" style="left:623px;top:1350px">Refer clients who are:</div>
<ul class="list">
  <li style="left:656px;top:1404px"><svg width="16" height="14"><path d="M2 12 C2 6 6 5 11 5 V2 L15 6.5 L11 11 V8 C7 8 4 9 2 12Z" fill="#333"/></svg>Homeowners</li>
  <li style="left:656px;top:1435px"><svg width="16" height="14"><path d="M2 12 C2 6 6 5 11 5 V2 L15 6.5 L11 11 V8 C7 8 4 9 2 12Z" fill="#333"/></svg>Pension card holders</li>
  <li style="left:656px;top:1466px"><svg width="16" height="14"><path d="M2 12 C2 6 6 5 11 5 V2 L15 6.5 L11 11 V8 C7 8 4 9 2 12Z" fill="#333"/></svg>Usually at home from 9am to 5pm</li>
  <li style="left:656px;top:1497px;white-space:nowrap"><svg width="16" height="14"><path d="M2 12 C2 6 6 5 11 5 V2 L15 6.5 L11 11 V8 C7 8 4 9 2 12Z" fill="#333"/></svg>Average to high electricity users (contact Brightfield Homes if unsure)</li>
</ul>

<h2 class="section-title abs center" style="top:1673px">WHO IS BRIGHTFIELD HOMES?</h2>
<p class="body-copy abs center" style="top:1729px">Over 20 Northvale councils have come together with support from the Northvale<br>State Government's Clean Power Futures Fund to run the Brightfield Home program.</p>
<div class="subhead abs center" style="top:1805px">What next?</div>
<p class="abs center" style="top:1849px;font:400 14px 'Open Sans',sans-serif">To refer clients or for further information, contact Doug Hollins at Brightfield Homes:</p>

<div class="contact-box abs">
  <svg class="abs" style="left:55px;top:19px" width="20" height="20" viewBox="0 0 20 20"><path d="M4 1 L8 1 L9 6 L6.5 7.5 C8 11 9.5 12.5 12.5 13.5 L14 11 L19 12 L19 16 C19 18 17 19 15 19 C7 18 2 13 1 5 C1 3 2 1 4 1Z" fill="#333"/></svg>
  <span style="left:89px">0400 555 123</span>
  <svg class="abs" style="left:270px;top:20px" width="24" height="18" viewBox="0 0 24 18"><rect x="1.5" y="1.5" width="21" height="15" fill="none" stroke="#333" stroke-width="2"/><path d="M2 2 L12 10 L22 2" fill="none" stroke="#333" stroke-width="2"/></svg>
  <span style="left:312px">doug.hollins@eastvale.example</span>
</div>

<footer class="site-footer abs">
  <div class="footer-title abs" style="left:128px;top:36px">Quick Links</div>
  <div class="footer-link abs" style="left:135px;top:88px">Home</div>
  <div class="footer-link abs" style="left:135px;top:119px">About Us</div>
  <div class="footer-link abs" style="left:135px;top:150px">How it works</div>
  <div class="footer-link abs" style="left:135px;top:181px">Who is Brightfield Home?</div>
  <div class="footer-link abs" style="left:135px;top:212px">Contact Us</div>

  <div class="footer-title abs" style="left:343px;top:36px">Newsletter</div>

  <div class="footer-title abs" style="left:635px;top:36px">Contact Us</div>
  <svg class="abs" style="left:641px;top:88px" width="12" height="16" viewBox="0 0 12 16"><path d="M6 1 C3 1 1 3 1 6 C1 10 6 15 6 15 C6 15 11 10 11 6 C11 3 9 1 6 1Z" fill="none" stroke="#222" stroke-width="1.6"/><circle cx="6" cy="6" r="2" fill="#222"/></svg>
  <div class="footer-text abs" style="left:667px;top:84px">Main Store 48 Harbour Road<br>North Fairview</div>
  <svg class="abs" style="left:641px;top:145px" width="13" height="13" viewBox="0 0 20 20"><path d="M4 1 L8 1 L9 6 L6.5 7.5 C8 11 9.5 12.5 12.5 13.5 L14 11 L19 12 L19 16 C19 18 17 19 15 19 C7 18 2 13 1 5 C1 3 2 1 4 1Z" fill="#222"/></svg>
  <div class="footer-text abs" style="left:667px;top:141px">(555)-010-2274</div>
  <svg class="abs" style="left:642px;top:177px" width="12" height="9" viewBox="0 0 12 9"><rect width="12" height="9" fill="#222"/><path d="M0 0 L6 5 L12 0" stroke="#fff" stroke-width="1.2" fill="none"/></svg>
  <div class="footer-text abs" style="left:667px;top:171px">info@brightfieldhomes.example</div>

  <div class="footer-title abs" style="left:892px;top:36px">Follow Us</div>
  <div class="social-sq abs" style="left:889px;top:84px;background:#1f4f93"></div>
  <div class="footer-text abs" style="left:932px;top:87px">Chatterbook</div>
  <div class="social-sq abs" style="left:889px;top:122px;background:#2ab0e6"></div>
  <div class="footer-text abs" style="left:932px;top:126px">Tweetline</div>
  <div class="social-sq abs" style="left:889px;top:157px;background:#c4221f"></div>
  <div class="footer-text abs" style="left:932px;top:161px">ViewTube</div>
  <div class="social-sq abs" style="left:889px;top:192px;background:#de3b2b"></div>
  <div class="footer-text abs" style="left:932px;top:196px">Circleplus</div>
</footer>
<div class="newsletter-input abs">Enter Email id</div>
<svg class="abs" style="left:476px;top:2078px" width="12" height="9" viewBox="0 0 12 9"><rect x=".5" y=".5" width="11" height="8" fill="none" stroke="#777"/><path d="M.5 .5 L6 5 L11.5 .5" stroke="#777" fill="none"/></svg>
<div class="newsletter-btn abs">Join Now</div>

<div class="copyright abs">Copyrights © 2017 - All Rights Reserved</div>

</body>
</html>
```